LinkedIn Banner Design for B2B Consulting Firm

Take the already developed logo (attached) and incorporate it into a creative banner design for placement on LinkedIn (the social media platform targeting business users). The banner will be used on the firm's company profile page on LinkedIn (not yet created).

```html
<!DOCTYPE html>
<html lang="en">
<head>
<meta charset="utf-8">
<title>Fractional Marketing Services – Company Profile Banner</title>
<link rel="stylesheet" href="https://fonts.googleapis.com/css2?family=Oswald:wght@500;600&family=Poppins:wght@400;600&display=swap">
<style>
  :root {
    --page-bg: #ffffff;
    --banner-bg: #d3d3d3;
    --banner-bg-light: #dedede;
    --banner-bg-dark: #c4c4c4;
    --ink-green: #1f3a2b;
    --ink-dark: #2b2f2c;
    --shadow: rgba(0, 0, 0, 0.28);
  }
  * { margin: 0; padding: 0; box-sizing: border-box; }
  html, body {
    width: 1200px;
    height: 1200px;
    overflow: hidden;
    background: var(--page-bg);
  }
  .canvas {
    position: relative;
    width: 1200px;
    height: 1200px;
  }
  .banner {
    position: absolute;
    left: 36px;
    top: 504px;
    width: 1128px;
    height: 191px;
    overflow: hidden;
    background: var(--banner-bg);
    box-shadow: 0 14px 22px var(--shadow);
  }
  .banner-backdrop {
    position: absolute;
    inset: 0;
    background: linear-gradient(90deg, var(--banner-bg-dark) 0%, var(--banner-bg-light) 35%, var(--banner-bg) 65%, var(--banner-bg-light) 100%);
  }
  .banner-copy {
    position: absolute;
    left: 229px;
    top: 62px;
    color: var(--ink-dark);
  }
  .headline {
    font-family: "Oswald", sans-serif;
    font-weight: 600;
    font-size: 33px;
    line-height: 1;
    letter-spacing: -0.3px;
    color: var(--ink-green);
    transform: scaleX(0.81);
    transform-origin: left center;
    white-space: nowrap;
  }
  .audience {
    margin-top: 3px;
    font-family: "Poppins", sans-serif;
    font-weight: 400;
    font-size: 17px;
    line-height: 1.02;
    color: var(--ink-dark);
    white-space: nowrap;
  }
  .audience-emphasis {
    display: block;
    font-weight: 600;
    letter-spacing: 4.4px;
  }
  .photo-collage {
    position: absolute;
    left: 0;
    top: 0;
    width: 1128px;
    height: 191px;
  }
</style>
</head>
<body>
<main class="canvas">
  <section class="banner">
    <div class="banner-backdrop" role="img" aria-label="Faded grey photo of business people in silhouette shaking hands in a bright office, with a faint network-line overlay"></div>

    <div class="banner-copy">
      <h1 class="headline">FRACTIONAL MARKETING SERVICES</h1>
      <p class="audience">FOR PRIVATE EQUITY FUNDS FAMILY OFFICES &amp;
        <span class="audience-emphasis">INVESTMENT BANKS</span>
      </p>
    </div>

    <svg class="photo-collage" viewBox="0 0 1128 191" xmlns="http://www.w3.org/2000/svg">
      <defs>
        <linearGradient id="photo-tone-a" x1="0" y1="0" x2="1" y2="1">
          <stop offset="0" stop-color="#9aa1a4"/>
          <stop offset="0.6" stop-color="#6b7174"/>
          <stop offset="1" stop-color="#3f4447"/>
        </linearGradient>
        <linearGradient id="photo-tone-b" x1="0" y1="0" x2="0" y2="1">
          <stop offset="0" stop-color="#8e9598"/>
          <stop offset="0.5" stop-color="#5c6367"/>
          <stop offset="1" stop-color="#7b8185"/>
        </linearGradient>
        <linearGradient id="photo-tone-c" x1="1" y1="0" x2="0" y2="1">
          <stop offset="0" stop-color="#a3a9ab"/>
          <stop offset="0.55" stop-color="#656b6e"/>
          <stop offset="1" stop-color="#3a3f42"/>
        </linearGradient>
      </defs>
      <g class="collage-panel" role="img" aria-label="Photo of a modern loft office lounge with sofa, plants and tall windows">
        <polygon points="745,15 854,15 777,157 660,157" fill="url(#photo-tone-a)"/>
      </g>
      <g class="collage-panel" role="img" aria-label="Photo of colleagues meeting around a desk with computer monitors">
        <polygon points="861,35 970,35 882,180 769,180" fill="url(#photo-tone-b)"/>
      </g>
      <g class="collage-panel" role="img" aria-label="Photo of a consultant working at a desk in an office with large windows">
        <polygon points="988,15 1104,15 1025,158 885,158" fill="url(#photo-tone-c)"/>
      </g>
    </svg>
  </section>
</main>
</body>
</html>
```